Business Card Design

Business Card for professional consulting firm working with large financial institutions.

Target Market(s)

Executive buyers

Industry/Entity Type

Banking

Contact Information for Business Card

Mild creativity wanted. Not boring, but do elaborate artwork.

Font styles to use
Serif
Sans Serif

Colors

Designer to choose colors to be used in the design.

Requirements
Must have
• Standard business card features - company name, individual name, telephone, website, email, locations.
Nice to have
• Two colors
Should not have
• too many colors, fancy printing, cartoons.

```html
<!DOCTYPE html>
<html lang="en">
<head>
<meta charset="utf-8">
<title>Halden Advisory business card</title>
<link rel="stylesheet" href="https://fonts.googleapis.com/css2?family=Tinos:wght@400&family=Roboto:wght@400&display=swap">
<style>
  :root {
    --backdrop: #b9b9b9;
    --card-light: #f3f3f3;
    --card-dark: #000000;
    --ink: #1a1a1a;
    --ink-soft: #4d4d4d;
    --ink-muted: #a8a8a8;
    --paper-white: #ffffff;
    --url-light: #e0e0e0;
  }
  * { margin: 0; padding: 0; box-sizing: border-box; }
  html, body { width: 1200px; height: 960px; overflow: hidden; }
  body { background: var(--backdrop); position: relative; }

  .card {
    position: absolute;
    width: 600px;
    height: 342px;
    box-shadow: 2px 3px 4px rgba(0,0,0,0.35);
  }
  .card--front { left: 322px; top: 108px; background: var(--card-light); }
  .card--back  { left: 320px; top: 493px; background: var(--card-dark); }

  .brand-name {
    position: absolute;
    font-family: "Tinos", "Times New Roman", serif;
    font-weight: 400;
    white-space: nowrap;
  }
  .card--front .brand-name {
    left: 32px; top: 54px;
    font-size: 30px;
    color: var(--ink);
  }
  .card--back .brand-name {
    left: 0; width: 600px; top: 146px;
    text-align: center;
    font-size: 34px;
    color: var(--paper-white);
  }

  .address, .contact-list {
    position: absolute;
    left: 32px;
    font-family: "Tinos", "Times New Roman", serif;
    font-size: 16px;
    color: var(--ink-soft);
    line-height: 19.5px;
  }
  .address { top: 197px; font-style: normal; }
  .contact-list { top: 244px; list-style: none; }
  .contact-list li { display: flex; align-items: center; gap: 7px; }
  .contact-list svg { width: 14px; height: 14px; flex: none; }

  .person {
    position: absolute;
    right: 32px; top: 226px;
    text-align: right;
    font-family: "Tinos", "Times New Roman", serif;
  }
  .person__name {
    font-size: 25px;
    color: var(--ink);
    transform: scaleX(0.88);
    transform-origin: right;
    line-height: 30px;
  }
  .person__title { font-size: 16px; color: var(--ink-muted); line-height: 18px; }

  .back-url {
    position: absolute;
    left: 0; width: 600px; top: 280px;
    text-align: center;
    font-family: "Roboto", Arial, sans-serif;
    font-size: 14px;
    letter-spacing: 5.2px;
    color: var(--url-light);
  }
</style>
</head>
<body>
  <section class="card card--front">
    <div class="brand-name">Halden Advisory</div>

    <address class="address">
      4120 Harbor Street<br>
      Juneau, Alaska 99801
    </address>

    <ul class="contact-list">
      <li>
        <svg viewBox="0 0 16 16" aria-hidden="true"><path fill="#1a1a1a" d="M3.6 1.2l2.3 2.7-1.3 1.6c.9 2 2.6 3.7 4.6 4.6l1.6-1.3 2.7 2.3-1.5 2.6C7 13.3 2.7 9 1 3.1z"/></svg>
        555 014 2938
      </li>
      <li>
        <svg viewBox="0 0 16 16" aria-hidden="true"><rect x="1" y="3.5" width="14" height="9" fill="#1a1a1a"/><path d="M1.5 4l6.5 5 6.5-5" fill="none" stroke="#f3f3f3" stroke-width="1.3"/></svg>
        info@haldenadvisory.com
      </li>
      <li>
        <svg viewBox="0 0 16 16" aria-hidden="true"><circle cx="8" cy="8" r="6.5" fill="none" stroke="#1a1a1a" stroke-width="1.4"/><ellipse cx="8" cy="8" rx="2.8" ry="6.5" fill="none" stroke="#1a1a1a" stroke-width="1.2"/><path d="M1.5 8h13" stroke="#1a1a1a" stroke-width="1.2"/></svg>
        www.haldenadvisory.com
      </li>
    </ul>

    <div class="person">
      <div class="person__name">Daniel Marsh</div>
      <div class="person__title">CEO/Founder</div>
    </div>
  </section>

  <section class="card card--back">
    <div class="brand-name">Halden Advisory</div>
    <div class="back-url">www.haldenadvisory.com</div>
  </section>
</body>
</html>
```